Business Card Re-Design/Update

We'd like to update out business cards. I've included our current "Style guide" which has the colour scheme of the organisation in it. I've also included the branding files with logos etc in them.

I've also included a copy of one of our existing cards so that you can see how ugly/dated they look. I'd like a fresh modern corporate look.

Target Market(s)

These are for our clients, potential clients, industry contacts - like all business cards

Contact Information for Business Card

Name
Position
Company Address - Level 1, 47 Fernby Street, Carlow Qld 4072
Direct Phone
mobile
Email
Website -www.korvalit.com.au
Logo

Colors

Designer to choose colors to be used in the design.

Requirements
Must have
• Main Logo
• Cards will need to be editable to be able to personalize them for each new employee.
Nice to have
• The MapOut, ShipWell, KeepSteady would be okay to have if they can be sensibly and professionally added to the look without detracting from the main imagery.
• Maybe they could go on the back of the card? will leave this to your creative discretion as to whether/where they fit.
Should not have
• Should not have decorative or script fonts

```html
<!DOCTYPE html>
<html lang="en">
<head>
<meta charset="utf-8">
<title>korvalIT business card</title>
<link rel="stylesheet" href="https://fonts.googleapis.com/css2?family=Roboto:wght@400;500;700&display=swap">
<style>
  :root {
    --page-bg: #e6e6e6;
    --card-bg: #fbfbfb;
    --brand-red: #b3262b;
    --band-light: #d65a5f;
    --band-mid: #c23c41;
    --band-dark: #a8232a;
    --ink: #1f1f1f;
    --ink-soft: #4a4a4a;
    --plan-green: #5d9c3a;
    --deliver-blue: #2a86c8;
    --sustain-magenta: #b5208f;
  }
  * { box-sizing: border-box; margin: 0; padding: 0; }
  html, body { width: 1200px; height: 960px; overflow: hidden; }
  body {
    background: var(--page-bg);
    font-family: "Roboto", Arial, sans-serif;
    position: relative;
  }
  .card {
    position: absolute;
    width: 600px;
    height: 343px;
    background: var(--card-bg);
    box-shadow: 2px 3px 5px rgba(0,0,0,0.35);
    overflow: hidden;
  }
  .card--front { left: 314px; top: 113px; }
  .card--back { left: 311px; top: 472px; }

  /* Front */
  .contact-list {
    position: absolute;
    left: 40px;
    top: 36px;
    list-style: none;
    color: var(--ink-soft);
    font-size: 14px;
    line-height: 19px;
  }
  .contact-list li { display: flex; align-items: flex-start; }
  .contact-list .icon { width: 24px; flex: none; display: flex; justify-content: flex-start; padding-top: 3px; }
  .contact-list .address { margin-bottom: 8px; }
  .person {
    position: absolute;
    right: 36px;
    top: 34px;
    text-align: right;
  }
  .person__name {
    color: var(--brand-red);
    font-size: 20px;
    font-weight: 500;
    line-height: 24px;
  }
  .person__role {
    color: var(--ink);
    font-size: 14px;
    line-height: 18px;
    margin-bottom: 9px;
  }
  .person__mobile {
    color: var(--ink-soft);
    font-size: 17px;
    font-weight: 700;
    line-height: 21px;
  }
  .person__email {
    color: var(--ink-soft);
    font-size: 14px;
    line-height: 19px;
  }
  .artwork-band {
    position: absolute;
    left: 0;
    bottom: 0;
    width: 600px;
    height: 190px;
    background: linear-gradient(100deg, var(--band-light) 0%, var(--band-mid) 50%, var(--band-dark) 100%);
  }
  .website {
    position: absolute;
    right: 34px;
    bottom: 26px;
    color: #ffffff;
    font-size: 13px;
    font-weight: 500;
    letter-spacing: 2.6px;
  }

  /* Back */
  .brand {
    position: absolute;
    left: 0;
    right: 0;
    top: 122px;
    display: flex;
    justify-content: center;
    align-items: center;
    gap: 16px;
  }
  .brand__mark {
    width: 56px;
    height: 56px;
    background: var(--brand-red);
  }
  .brand__name {
    color: var(--ink);
    font-size: 50px;
    font-weight: 700;
    letter-spacing: -1px;
    line-height: 1;
  }
  .services {
    position: absolute;
    left: 46px;
    right: 56px;
    top: 278px;
    display: flex;
    justify-content: space-between;
    list-style: none;
  }
  .service {
    display: flex;
    align-items: center;
    gap: 8px;
    font-size: 24px;
    font-weight: 500;
    line-height: 1;
  }
  .service__dot { width: 20px; height: 20px; }
  .service--plan { color: var(--plan-green); }
  .service--plan .service__dot { background: var(--plan-green); }
  .service--deliver { color: var(--deliver-blue); }
  .service--deliver .service__dot { background: var(--deliver-blue); }
  .service--sustain { color: var(--sustain-magenta); }
  .service--sustain .service__dot { background: var(--sustain-magenta); }
</style>
</head>
<body>

<section class="card card--front">
  <ul class="contact-list">
    <li class="address">
      <span class="icon">
        <svg width="11" height="15" viewBox="0 0 11 15"><path d="M5.5 0C2.5 0 0 2.4 0 5.4 0 9.2 5.5 15 5.5 15S11 9.2 11 5.4C11 2.4 8.5 0 5.5 0Zm0 7.6a2.2 2.2 0 1 1 0-4.4 2.2 2.2 0 0 1 0 4.4Z" fill="var(--brand-red)"/></svg>
      </span>
      <span>Level 1, 47 Fernby Street<br>Carlow Qld 4072</span>
    </li>
    <li>
      <span class="icon">
        <svg width="13" height="13" viewBox="0 0 24 24"><path d="M6.6 10.8c1.4 2.8 3.8 5.1 6.6 6.6l2.2-2.2c.3-.3.7-.4 1-.2 1.1.4 2.3.6 3.6.6.6 0 1 .4 1 1V20c0 .6-.4 1-1 1C10.6 21 3 13.4 3 4c0-.6.4-1 1-1h3.5c.6 0 1 .4 1 1 0 1.3.2 2.5.6 3.6.1.3 0 .7-.2 1L6.6 10.8Z" fill="var(--brand-red)"/></svg>
      </span>
      <span>+61 (0)7 5550 1420</span>
    </li>
    <li>
      <span class="icon">
        <svg width="13" height="13" viewBox="0 0 24 24"><path d="M6.6 10.8c1.4 2.8 3.8 5.1 6.6 6.6l2.2-2.2c.3-.3.7-.4 1-.2 1.1.4 2.3.6 3.6.6.6 0 1 .4 1 1V20c0 .6-.4 1-1 1C10.6 21 3 13.4 3 4c0-.6.4-1 1-1h3.5c.6 0 1 .4 1 1 0 1.3.2 2.5.6 3.6.1.3 0 .7-.2 1L6.6 10.8Z" fill="var(--brand-red)"/></svg>
      </span>
      <span>+61 (0)7 5550 1437</span>
    </li>
    <li>
      <span class="icon">
        <svg width="16" height="13" viewBox="0 0 16 13"><rect x="3" y="0" width="10" height="5" fill="var(--brand-red)"/><rect x="0" y="5" width="16" height="8" rx="1.5" fill="var(--brand-red)"/><rect x="4" y="8" width="8" height="2" fill="#fbfbfb"/></svg>
      </span>
      <span>+61 (0)7 5550 1499</span>
    </li>
  </ul>

  <div class="person">
    <p class="person__name">DANA WHITCOMBE</p>
    <p class="person__role">Business Development Manager</p>
    <p class="person__mobile">+61 (0)400 555 182</p>
    <p class="person__email">dwhitcombe@korvalit.com.au</p>
  </div>

  <div class="artwork-band" role="img" aria-label="Red faceted low-poly artwork band"></div>

  <p class="website">www.korvalit.com.au</p>
</section>

<section class="card card--back">
  <div class="brand">
    <span class="brand__mark" aria-hidden="true"></span>
    <span class="brand__name">korvalIT</span>
  </div>
  <ul class="services">
    <li class="service service--plan"><span class="service__dot" aria-hidden="true"></span>MapOut</li>
    <li class="service service--deliver"><span class="service__dot" aria-hidden="true"></span>ShipWell</li>
    <li class="service service--sustain"><span class="service__dot" aria-hidden="true"></span>KeepSteady</li>
  </ul>
</section>

</body>
</html>
```